Business card design for my company.
I would like the card's background colour to be black. You can also see our web site to get an idea of our brand. https://www.tmwhomecrafting.com.au/
- Name
- Email

```html
<!DOCTYPE html>
<html lang="en">
<head>
<meta charset="utf-8">
<title>TMW Home Crafting – Business Card</title>
<link rel="stylesheet" href="https://fonts.googleapis.com/css2?family=Open+Sans:wght@300;400;600&display=swap">
<style>
  :root {
    --page-bg: #1f1f1f;
    --card-bg: #38383a;
    --card-bg-upper: #424244;
    --card-back-bg: #323233;
    --accent-green: #1f8a45;
    --accent-green-dark: #17693a;
    --text-white: #ffffff;
    --text-soft: #d6d6d6;
  }
  * { box-sizing: border-box; margin: 0; padding: 0; }
  html, body {
    width: 1200px;
    height: 1153px;
    overflow: hidden;
    background: var(--page-bg);
    font-family: "Open Sans", Arial, sans-serif;
  }
  .canvas {
    position: relative;
    width: 1200px;
    height: 1153px;
  }
  .card {
    position: absolute;
    left: 200px;
    width: 800px;
    height: 430px;
    overflow: hidden;
    box-shadow: 0 14px 30px rgba(0,0,0,0.55);
  }
  .card-front { top: 112px; background: var(--card-bg); }
  .card-back  { top: 590px; background: var(--card-back-bg); }

  .front-shapes { position: absolute; inset: 0; width: 100%; height: 100%; }

  .person { position: absolute; left: 56px; top: 36px; color: var(--text-white); }
  .person-name { font-size: 32px; font-weight: 400; letter-spacing: 0.3px; line-height: 1.2; }
  .person-title { font-size: 14px; font-weight: 400; color: var(--text-soft); margin-top: 2px; }

  .contact-list {
    position: absolute; left: 56px; top: 318px;
    list-style: none; color: var(--text-white);
    font-size: 17px; line-height: 1;
  }
  .contact-item { display: flex; align-items: center; gap: 14px; height: 23px; }
  .contact-icon { width: 14px; height: 14px; flex: none; }

  .front-brand {
    position: absolute; right: 48px; top: 345px;
    display: flex; align-items: center; gap: 8px;
    color: var(--text-white); font-size: 15px; font-weight: 600; letter-spacing: 1px;
  }
  .brand-square { width: 10px; height: 10px; background: var(--accent-green); }

  .back-brand {
    position: absolute; inset: 0;
    display: flex; align-items: center; justify-content: center; gap: 20px;
    color: var(--text-white); font-size: 48px; font-weight: 600; letter-spacing: 4px;
  }
  .back-brand .brand-square { width: 24px; height: 24px; }
</style>
</head>
<body>
<div class="canvas">

  <section class="card card-front">
    <svg class="front-shapes" viewBox="0 0 800 430" preserveAspectRatio="none" aria-hidden="true">
      <polygon points="0,0 552,0 0,222" fill="var(--card-bg-upper)"/>
      <polygon points="552,0 800,0 800,142" fill="var(--card-bg-upper)"/>
      <polygon points="0,222 552,0 0,246" fill="var(--accent-green)"/>
      <polygon points="552,0 800,142 800,186" fill="var(--accent-green-dark)"/>
      <polygon points="552,0 800,142 800,152" fill="var(--accent-green)"/>
    </svg>

    <div class="person">
      <p class="person-name">Liam Harcourt</p>
      <p class="person-title">General Manager</p>
    </div>

    <ul class="contact-list">
      <li class="contact-item">
        <svg class="contact-icon" viewBox="0 0 24 24"><path fill="var(--accent-green)" d="M6.6 10.8a15 15 0 0 0 6.6 6.6l2.2-2.2c.3-.3.7-.4 1-.2 1.1.4 2.3.6 3.6.6.6 0 1 .4 1 1V20c0 .6-.4 1-1 1A17 17 0 0 1 3 4c0-.6.4-1 1-1h3.5c.6 0 1 .4 1 1 0 1.3.2 2.5.6 3.6.1.3 0 .7-.2 1z"/></svg>
        <span>0400 555 017</span>
      </li>
      <li class="contact-item">
        <svg class="contact-icon" viewBox="0 0 24 24"><path fill="var(--accent-green)" d="M2 5h20v14H2z"/><path fill="none" stroke="var(--card-bg)" stroke-width="2" d="M2 6l10 7 10-7"/></svg>
        <span>info@tmwhomecrafting.com.au</span>
      </li>
      <li class="contact-item">
        <svg class="contact-icon" viewBox="0 0 24 24"><path fill="var(--accent-green)" d="M12 2a7 7 0 0 0-7 7c0 5.3 7 13 7 13s7-7.7 7-13a7 7 0 0 0-7-7zm0 9.5A2.5 2.5 0 1 1 12 6.5a2.5 2.5 0 0 1 0 5z"/></svg>
        <span>Westmere Bay, Northvale</span>
      </li>
    </ul>

    <div class="front-brand">
      <span class="brand-square"></span>
      <span>TMW HOME CRAFTING</span>
    </div>
  </section>

  <section class="card card-back">
    <div class="back-brand">
      <span class="brand-square"></span>
      <span>TMW HOME CRAFTING</span>
    </div>
  </section>

</div>
</body>
</html>
```